Boutique custom software development company needs new business card

Our nearly 20 year old custom software development company would like to better include the fact that we are now providing Bitcoin services. These new services are B2B include education (how to acquire and securely hold Bitcoin) and integrating Bitcoin payments into existing ecommerce sites or other existing systems. Please keep the card clean and simple. Attached is our current design and some other files. vextorial.com

Target Market(s)

businesses owners interested in long term relationship

Industry/Entity Type

Custom software development and Bitcoin

Contact Information for Business Card

Dale Parker, dale@vextorial.com, vextorial.com, (888) 555-VXTRL

Font styles to use
Other font styles liked:
• monospace

Requirements
Must have
• double-sided
Nice to have
• clean and simple
Should not have
• physical address

```html
<!DOCTYPE html>
<html lang="en">
<head>
<meta charset="utf-8">
<title>Vextorial Business Card</title>
<link href="https://fonts.googleapis.com/css2?family=Montserrat:wght@400;500;700;800&family=Lato:wght@400&display=swap" rel="stylesheet">
<style>
  :root {
    --bg: #d4d7d8;
    --paper: #f7f7f5;
    --blue: #2c67b1;
    --orange: #e8701c;
    --ink: #3a3a3a;
    --grey: #555555;
  }
  * { box-sizing: border-box; margin: 0; padding: 0; }
  html, body { width: 1200px; height: 905px; overflow: hidden; }
  body {
    background: var(--bg);
    font-family: "Montserrat", sans-serif;
    display: flex;
    align-items: center;
    justify-content: center;
    gap: 40px;
  }
  .card {
    position: relative;
    width: 520px;
    height: 297px;
    overflow: hidden;
    box-shadow: 0 10px 28px rgba(0,0,0,0.18);
  }
  .card--front { background: var(--paper); }
  .card--back {
    background: var(--blue);
    display: flex;
    flex-direction: column;
    align-items: center;
    justify-content: center;
  }
  .front-wave { position: absolute; inset: 0; width: 100%; height: 100%; }
  .brand { position: absolute; left: 34px; top: 70px; }
  .brand__name {
    font-weight: 800;
    font-size: 36px;
    letter-spacing: 0.5px;
    color: var(--blue);
    line-height: 1;
  }
  .brand__tagline {
    font-family: "Lato", sans-serif;
    font-size: 13.5px;
    color: var(--blue);
    margin-top: 6px;
    letter-spacing: -0.2px;
  }
  .divider {
    position: absolute;
    left: 262px;
    top: 62px;
    width: 1px;
    height: 118px;
    background: var(--orange);
  }
  .contact { position: absolute; left: 284px; top: 68px; }
  .contact__name {
    font-weight: 700;
    font-size: 17px;
    letter-spacing: 1.5px;
    text-transform: uppercase;
  }
  .contact__first { color: var(--orange); }
  .contact__last { color: var(--blue); }
  .contact__role {
    font-size: 11.5px;
    color: var(--grey);
    letter-spacing: 0.5px;
    margin-top: 1px;
  }
  .contact__list { list-style: none; margin-top: 12px; }
  .contact__item {
    display: flex;
    align-items: center;
    gap: 6px;
    font-size: 11.5px;
    color: var(--ink);
    letter-spacing: 0.6px;
    line-height: 19px;
  }
  .contact__icon { width: 10px; height: 10px; fill: var(--blue); flex: none; }
  .back__name {
    font-weight: 800;
    font-size: 58px;
    letter-spacing: 1px;
    color: #f4f4f4;
    line-height: 1;
  }
  .back__tagline {
    font-family: "Lato", sans-serif;
    font-size: 21px;
    color: #f4f4f4;
    margin-top: 10px;
    letter-spacing: -0.3px;
  }
</style>
</head>
<body>
  <section class="card card--front">
    <svg class="front-wave" viewBox="0 0 520 297" preserveAspectRatio="none" aria-hidden="true">
      <path d="M0,118 C140,210 340,274 520,272 L520,297 L0,297 Z" fill="var(--blue)"/>
      <path d="M90,162 C220,228 380,258 520,254 L520,263 C370,265 210,232 90,162 Z" fill="var(--orange)"/>
    </svg>
    <div class="brand">
      <div class="brand__name">VEXTORIAL</div>
      <div class="brand__tagline">developer of custom applications</div>
    </div>
    <div class="divider"></div>
    <div class="contact">
      <div class="contact__name"><span class="contact__first">Dale</span> <span class="contact__last">Parker</span></div>
      <div class="contact__role">Owner</div>
      <ul class="contact__list">
        <li class="contact__item">
          <svg class="contact__icon" viewBox="0 0 10 10"><path d="M2,0.5 L3.6,2.6 L2.8,3.6 C3.4,5 4.9,6.4 6.4,7.2 L7.4,6.4 L9.5,8 L8.4,9.5 C4.5,9 1,5.5 0.5,1.6 Z"/></svg>
          (888) 555-VXTRL
        </li>
        <li class="contact__item">
          <svg class="contact__icon" viewBox="0 0 10 10"><path d="M0,2 H10 V8.5 H0 Z M0.8,2.6 L5,5.8 L9.2,2.6" fill="var(--blue)" stroke="#fff" stroke-width="0.7"/></svg>
          dale@vextorial.com
        </li>
        <li class="contact__item">
          <svg class="contact__icon" viewBox="0 0 10 10"><circle cx="5" cy="5" r="4.6"/><path d="M0.6,5 H9.4 M5,0.4 C2.8,3 2.8,7 5,9.6 M5,0.4 C7.2,3 7.2,7 5,9.6" fill="none" stroke="#fff" stroke-width="0.6"/></svg>
          www.vextorial.com
        </li>
      </ul>
    </div>
  </section>

  <section class="card card--back">
    <div class="back__name">VEXTORIAL</div>
    <div class="back__tagline">developer of custom applications</div>
  </section>
</body>
</html>
```